Vantro cards

I am in the auto motive, transportation business I would like a business card that is Something cool, modern edgy, having to do with car culture. I offer towing service for high and exotic cars. I also provide towing for collisions and car accidents. I offer open and enclosed transport nationwide.

Target Market(s)

Car culture people high end auto collectors

Industry/Entity Type

Towing car carrier

Contact Information for Business Card

My company colors black yellow and silver

Font styles to use
Serif

```html
<!DOCTYPE html>
<html lang="en">
<head>
<meta charset="utf-8">
<title>Vantro Cards</title>
<link rel="stylesheet" href="https://fonts.googleapis.com/css2?family=Alfa+Slab+One&family=Poppins:wght@300;400&display=swap">
<style>
  :root {
    --ink: #111111;
    --paper: #ffffff;
    --yellow: #f7dc4d;
    --yellow-deep: #d9b92a;
    --yellow-light: #fbe97e;
    --rule: #9a9a9a;
    --backdrop: #2a2a2a;
  }
  * { box-sizing: border-box; margin: 0; padding: 0; }
  html, body { width: 1200px; height: 1108px; overflow: hidden; }
  body {
    background: var(--backdrop);
    display: flex;
    align-items: center;
    justify-content: center;
    gap: 80px;
  }
  .card {
    width: 440px;
    height: 770px;
    border-radius: 26px;
    overflow: hidden;
    position: relative;
  }
  .card-front {
    background: var(--paper);
    color: var(--ink);
    display: flex;
    flex-direction: column;
    align-items: center;
    padding-top: 150px;
    font-family: "Poppins", sans-serif;
  }
  .brand {
    display: flex;
    align-items: center;
    gap: 16px;
    height: 200px;
  }
  .brand-mark {
    width: 30px;
    height: 30px;
    background: var(--yellow);
  }
  .brand-name {
    font-family: "Alfa Slab One", serif;
    font-size: 66px;
    color: var(--ink);
    letter-spacing: 1px;
  }
  .person-name {
    margin-top: 50px;
    font-family: "Alfa Slab One", serif;
    font-size: 34px;
    letter-spacing: 1px;
    text-transform: uppercase;
  }
  .person-role {
    font-weight: 300;
    font-size: 19px;
    letter-spacing: 2px;
    text-transform: uppercase;
    margin-top: -2px;
  }
  .icon-row {
    display: flex;
    align-items: center;
    gap: 12px;
    margin-top: 16px;
    width: 300px;
  }
  .icon-row::before, .icon-row::after {
    content: "";
    flex: 1;
    height: 1px;
    background: var(--rule);
  }
  .icon {
    width: 34px;
    height: 34px;
    background: var(--ink);
    border-radius: 5px;
    padding: 4px;
  }
  .icon svg { width: 100%; height: 100%; display: block; }
  .contact {
    margin-top: 10px;
    text-align: center;
    font-size: 21px;
    line-height: 1.3;
  }
  .divider {
    width: 300px;
    height: 1px;
    background: var(--rule);
    margin: 18px 0 14px;
  }
  .address {
    text-align: center;
    font-size: 21px;
    line-height: 1.3;
  }
  .card-back {
    background: linear-gradient(155deg, var(--yellow-light) 0%, var(--yellow) 45%, var(--yellow-deep) 100%);
    display: flex;
    align-items: flex-end;
    justify-content: center;
    padding-bottom: 190px;
  }
  .back-pattern {
    position: absolute;
    inset: 0;
  }
  .back-name {
    position: relative;
    font-family: "Alfa Slab One", serif;
    font-size: 34px;
    color: var(--ink);
  }
</style>
</head>
<body>
  <section class="card card-front">
    <div class="brand">
      <span class="brand-mark"></span>
      <span class="brand-name">Vantro</span>
    </div>
    <h1 class="person-name">Marcus Hale</h1>
    <p class="person-role">Managing Director</p>
    <div class="icon-row">
      <span class="icon">
        <svg viewBox="0 0 24 24"><rect width="24" height="24" rx="3" fill="#f7dc4d"/><path d="M7 5l3 3-2 2c1 2 3 4 5 5l2-2 3 3-2 3C10 18 6 14 5 8z" fill="#111"/></svg>
      </span>
      <span class="icon">
        <svg viewBox="0 0 24 24"><rect width="24" height="24" rx="3" fill="#f7dc4d"/><rect x="4" y="7" width="16" height="11" fill="none" stroke="#111" stroke-width="1.6"/><path d="M4 7l8 6 8-6" fill="none" stroke="#111" stroke-width="1.6"/></svg>
      </span>
      <span class="icon">
        <svg viewBox="0 0 24 24"><rect width="24" height="24" rx="3" fill="#f7dc4d"/><circle cx="12" cy="12" r="7" fill="none" stroke="#111" stroke-width="1.6"/><path d="M5 12h14M12 5c-3 4-3 10 0 14M12 5c3 4 3 10 0 14" fill="none" stroke="#111" stroke-width="1.2"/></svg>
      </span>
    </div>
    <p class="contact">044-318 274 650<br>info@vantrotow.com<br>www.vantrotow.com</p>
    <div class="divider"></div>
    <p class="address">421, Address line goes here<br>45452,Country Name</p>
  </section>

  <section class="card card-back">
    <div class="back-pattern" role="img" aria-label="Repeating embossed pattern of flatbed tow trucks in tonal gold"></div>
    <span class="back-name">Vantro</span>
  </section>
</body>
</html>
```